Fresh, modern, fun business card for pediatric dental practice

Need a business card for fresh, modern, fun pediatric dental practice

Clean look that matches our website's font and colors

We prefer the look of curved corners on business cards

Target Market(s)

parents (mothers) of young children, professionals, mid-high class

Industry/Entity Type

Dental

Contact Information for Business Card

Maplebrook Pediatric Dentistry
482 Quarry Lane
Suite 517
Alder Springs, PA 17000
717.555.0193
www.maplebrookkidsdental.example

Mei-Ran Tsai, DMD
Corinne Walbeck, DMD
(we are working on our email address, but we would like that on the card as well)

Font styles to use
Sans Serif

Requirements
Must have
• All info; we would also like to make cards for individual staff members
• colors from our website and color palatte, attatched
• use same font and design as website for branding
Nice to have
• clean, simple card that has a pop of color
• we would like to see a few designs with our tag line "where smiles get brighter"
• we are not sure if we want to have it on there or not
• we would like to see a few designs incorporating the ribbon graphic on our website where the word WELCOME is

```html
<!DOCTYPE html>
<html lang="en">
<head>
<meta charset="utf-8">
<title>Maplebrook Pediatric Dentistry – Business Card</title>
<link rel="stylesheet" href="https://fonts.googleapis.com/css2?family=Lato:wght@400;700&family=Raleway:wght@500&display=swap">
<style>
  :root {
    --backdrop: #ecebe8;
    --sun-yellow: #f6bb28;
    --berry: #d13497;
    --disc: #f1f2f2;
    --disc-shade: #dfe1e2;
    --brand-orange: #f2a31a;
    --ink-light: #ffffff;
  }
  * { margin: 0; padding: 0; box-sizing: border-box; }
  html, body {
    width: 1200px;
    height: 900px;
    overflow: hidden;
    background: var(--backdrop);
  }
  .canvas {
    position: relative;
    width: 1200px;
    height: 900px;
  }
  .card {
    position: absolute;
    left: 180px;
    top: 192px;
    width: 840px;
    height: 516px;
    border-radius: 16px;
    overflow: hidden;
    background: var(--sun-yellow);
    box-shadow: 0 10px 30px rgba(0,0,0,0.12);
  }
  .card__accent-band {
    position: absolute;
    top: 0;
    right: 0;
    width: 240px;
    height: 100%;
    background: var(--berry);
  }
  .card__brand-disc {
    position: absolute;
    left: 390px;
    top: 50px;
    width: 420px;
    height: 420px;
    border-radius: 50%;
    background: radial-gradient(circle at 40% 35%, var(--disc) 55%, var(--disc-shade) 100%);
    display: flex;
    align-items: center;
    justify-content: center;
  }
  .brand-name {
    font-family: "Lato", sans-serif;
    font-weight: 700;
    font-size: 40px;
    line-height: 1.15;
    color: var(--brand-orange);
    text-align: center;
  }
  .doctors {
    position: absolute;
    left: 39px;
    top: 58px;
    font-family: "Raleway", sans-serif;
    font-weight: 500;
    font-size: 24px;
    line-height: 40px;
    letter-spacing: 0.3px;
    color: var(--ink-light);
    text-transform: uppercase;
  }
  .address {
    position: absolute;
    left: 40px;
    top: 264px;
    font-family: "Lato", sans-serif;
    font-size: 21px;
    line-height: 30px;
    color: var(--ink-light);
    font-style: normal;
  }
  .contact-list {
    position: absolute;
    left: 38px;
    top: 344px;
    list-style: none;
    font-family: "Lato", sans-serif;
    font-size: 20px;
    line-height: 30px;
    color: var(--ink-light);
  }
  .contact-list li {
    display: flex;
    align-items: center;
    gap: 7px;
  }
  .contact-icon {
    width: 15px;
    height: 15px;
    flex: none;
  }
</style>
</head>
<body>
<main class="canvas">
  <section class="card" aria-label="Business card">
    <div class="card__accent-band"></div>
    <div class="card__brand-disc">
      <p class="brand-name">Maplebrook<br>Pediatric Dentistry</p>
    </div>

    <div class="doctors">
      <p>Mei-Ran Tsai, DMD</p>
      <p>Corinne Walbeck, DMD</p>
    </div>

    <address class="address">
      482 Quarry Lane<br>
      Suite 517&nbsp; Alder Springs, PA 17000
    </address>

    <ul class="contact-list">
      <li>
        <svg class="contact-icon" viewBox="0 0 16 16" aria-hidden="true">
          <path fill="#fff" d="M2 6c0-2 2.5-3 6-3s6 1 6 3v1h-3V5.5H5V7H2z M4 8h8l1.5 5h-11z"/>
        </svg>
        717.555.0193
      </li>
      <li>
        <svg class="contact-icon" viewBox="0 0 16 16" aria-hidden="true">
          <rect x="1.5" y="3.5" width="13" height="9" fill="#fff"/>
          <path d="M1.5 3.5 8 9l6.5-5.5" fill="none" stroke="#f6bb28" stroke-width="1.3"/>
        </svg>
        Mei-ran@maplebrookkidsdental.example
      </li>
      <li>
        <svg class="contact-icon" viewBox="0 0 16 16" aria-hidden="true">
          <rect x="1.5" y="3.5" width="13" height="9" fill="#fff"/>
          <path d="M1.5 3.5 8 9l6.5-5.5" fill="none" stroke="#f6bb28" stroke-width="1.3"/>
        </svg>
        Corinne@maplebrookkidsdental.example
      </li>
      <li>
        <svg class="contact-icon" viewBox="0 0 16 16" aria-hidden="true">
          <circle cx="8" cy="8" r="6.5" fill="#fff"/>
          <path d="M5 5.5c1.5 0 2 1 1.5 2s.5 2 1.5 2.5M10 4c-.5 1 0 2 1.2 2.3" fill="none" stroke="#f6bb28" stroke-width="1.3"/>
        </svg>
        www.maplebrookkidsdental.example
      </li>
    </ul>
  </section>
</main>
</body>
</html>
```